Redesign kavrin.ch agency website for unique design with speed and conversion

We want to redesign our website kavrin.ch. Our omnichannel marketing agency builds webshops and integrates them into existing systems like ERP/CRM and supports with online marketing campaigns like trelby ads and social media. The target of the redesign is to get a great look and feel for customers to see directly what we do, (please design something for our three focus areas eCommerce, Online marketing and Integration)
and to improve the pages speed drastically for SEO. Please see our attachment.
B2B
eCommerce Agency
Coded - Design and coding required
5+ page

```html
<!DOCTYPE html>
<html lang="en">
<head>
<meta charset="utf-8">
<title>kavrin.ch – Online Marketing Agency</title>
<link rel="stylesheet" href="https://fonts.googleapis.com/css2?family=Poppins:wght@400;500;600;700&display=swap">
<style>
:root{
  --green:#55e61f;
  --green-light:#b9f77e;
  --dark:#272b28;
  --dark-2:#1f2320;
  --ink:#1c1c1c;
  --text:#333;
  --mist:#e9efea;
  --white:#fff;
}
*{box-sizing:border-box;margin:0;padding:0}
html,body{width:1200px;height:5324px;overflow:hidden}
body{font-family:'Poppins',sans-serif;color:var(--text);background:var(--white);position:relative}
.abs{position:absolute}
.btn{position:absolute;background:var(--green);color:#fff;font-size:15px;font-weight:500;display:flex;align-items:center;justify-content:center;text-transform:uppercase;letter-spacing:.3px}
.center{left:0;right:0;text-align:center}
h2{font-weight:500;font-size:23px;color:var(--ink);text-transform:uppercase}

/* header */
.topbar{position:absolute;top:0;left:0;width:1200px;height:46px}
.toplinks{position:absolute;top:0;left:412px;height:46px;display:flex;gap:0;align-items:center;font-size:13px;color:#ddd}
.toplinks span{width:96px;text-align:center}
.topphone{position:absolute;top:0;left:1035px;height:46px;display:flex;align-items:center;gap:8px;color:#fff;font-size:14px;font-weight:500}
.header{position:absolute;top:46px;left:0;width:1200px;height:94px}
.logo{position:absolute;font-weight:700;color:var(--green);letter-spacing:3px}
.nav{position:absolute;top:84px;font-size:15px;font-weight:500;color:#222;text-transform:uppercase}
.nav.active{color:var(--green);border-bottom:2px solid var(--green);padding-bottom:2px}

/* hero */
.hero{position:absolute;top:140px;left:0;width:1200px;height:572px;background:linear-gradient(100deg,#161a18 0%,#2e3430 45%,#4a504b 70%,#2a2f2c 100%)}
.hero h1{position:absolute;left:108px;top:164px;font-size:35px;line-height:45px;color:#fff;font-weight:700;text-transform:uppercase}
.hero p{position:absolute;left:112px;top:262px;font-size:21px;line-height:27px;color:#fff;font-weight:500}
.arrow{position:absolute;top:240px;color:#fff;font-size:30px}
.dots{position:absolute;display:flex;gap:20px}
.dots i{width:11px;height:11px;border-radius:50%;background:var(--green-light);opacity:.6}
.dots i.on{background:var(--green);opacity:1}

/* intro */
.intro{position:absolute;top:712px;left:0;width:1200px;height:431px;background:linear-gradient(90deg,#fff 0%,#f4f6f4 60%,#e7ebe8 100%)}
.intro p{position:absolute;left:150px;width:900px;top:116px;font-size:16px;line-height:25.5px;text-align:center;color:#222}

/* services */
.services{position:absolute;top:1143px;left:0;width:1200px;height:692px;background:var(--dark)}
.services h2{color:#fff}
.card{position:absolute;top:179px;width:306px;height:395px;border:2px solid #6a6e6a;text-align:center;color:#fff}
.card.featured{border:3px solid var(--green)}
.card .icon{position:absolute;left:93px;top:28px;width:120px;height:100px;background:#cfd2cf;border-radius:10px;opacity:.85}
.card h3{position:absolute;top:148px;left:10px;right:10px;font-size:19px;line-height:26px;font-weight:500}
.card p{position:absolute;top:212px;left:14px;right:14px;font-size:14px;line-height:21px;color:#e4e4e4}
.card .btn{left:90px;width:126px;height:38px;top:328px;font-size:13px}

/* value */
.value{position:absolute;top:1835px;left:0;width:1200px;height:655px;background:linear-gradient(90deg,#e9efea,#dfe6e0)}
.value p{position:absolute;top:158px;font-size:19px;line-height:28px;color:#111;font-weight:500}
.node{position:absolute;width:116px;height:116px;border-radius:50%;border:2px dotted #222;display:flex;align-items:center;justify-content:center}
.node b{width:96px;height:96px;border-radius:50%;background:var(--dark);display:block}
.node.on b{background:var(--green)}
.nlabel{position:absolute;font-size:15px;font-weight:500;color:#222;text-transform:uppercase}

/* contact */
.contact{position:absolute;top:2490px;left:0;width:1200px;height:681px;background:linear-gradient(90deg,#2b302d 0%,#3b403c 50%,#555a56 75%,#2c312e 100%)}
.form{position:absolute;left:114px;top:92px;width:479px;height:507px;background:rgba(34,38,35,.92)}
.form h3{position:absolute;top:56px;left:0;right:0;text-align:center;color:#fff;font-size:19px;font-weight:600}
.field{position:absolute;border:1px solid #8a8e8a;color:#fff;font-size:15px;padding:9px 20px}
.form .btn{left:179px;top:505px;width:125px;height:40px;font-size:16px}

/* feedback */
.feedback{position:absolute;top:3171px;left:0;width:1200px;height:637px;background:#fff}
.fcard{position:absolute;left:209px;top:157px;width:779px;height:360px;background:#fff;box-shadow:0 2px 14px rgba(0,0,0,.14)}
.thumb{position:absolute;left:8px;width:126px;height:108px;background:#e9e9e9}
.thumb b{position:absolute;left:20px;top:10px;width:86px;height:86px;border-radius:50%;background:#7d807d}
.thumb.on{border-left:6px solid var(--green);left:0;width:134px}
.thumb.on b{background:linear-gradient(#d7d7d7,#9a9a9a)}
.quote{position:absolute;left:184px;top:20px}
.fcard .lead{position:absolute;left:184px;top:112px;width:460px;font-size:20px;line-height:26px;color:#111;font-weight:500}
.fcard .body{position:absolute;left:184px;top:175px;width:580px;font-size:16px;line-height:25px;color:#222}
.fcard .who{position:absolute;left:186px;top:269px;font-size:16px;color:#222;font-weight:500}
.fcard .role{position:absolute;left:186px;top:295px;font-size:13px;line-height:20px;color:#555}

/* team */
.team{position:absolute;top:3808px;left:0;width:1200px;height:779px;background:var(--dark)}
.team h2{color:#fff}
.member{position:absolute;top:163px;width:338px;text-align:center;color:#fff}
.member .photo{width:338px;height:399px;background:linear-gradient(180deg,#d4d6d4,#a9aca9 60%,#3a3e3b)}
.member h3{margin-top:36px;font-size:25px;font-weight:500}
.member .role{font-size:22px;margin-top:6px}
.member .mail{font-size:15px;margin-top:8px;display:flex;justify-content:center;align-items:center;gap:10px}

/* partners */
.partners{position:absolute;top:4587px;left:0;width:1200px;height:341px;background:#fff}
.pbox{position:absolute;top:103px;width:224px;height:128px;border:2px solid #dcdcdc;display:flex;align-items:center;justify-content:center}
.pbox b{display:block;width:140px;height:36px;border-radius:6px;background:#d9dcd9}

/* footer */
.footer{position:absolute;top:4928px;left:0;width:1200px;height:396px;background:var(--dark-2);color:#fff}
.fcol{position:absolute;top:93px}
.fcol h4{font-size:18px;font-weight:600;text-transform:uppercase;margin-bottom:20px}
.fcol a{display:block;font-size:15px;color:#fff;text-decoration:none;line-height:35.5px}
.finfo{position:absolute;left:112px;font-size:15px;line-height:22px;display:flex;gap:12px;align-items:flex-start}
.copy{position:absolute;left:112px;top:361px;font-size:12px;color:#ddd}
</style>
</head>
<body>

<!-- header -->
<svg class="topbar" width="1200" height="46" viewBox="0 0 1200 46">
  <polygon points="380,0 1200,0 1200,46 345,46" fill="#242826"/>
  <polygon points="1010,0 1200,0 1200,46 985,46" fill="#1a1d1b"/>
  <polygon points="1000,0 1010,0 985,46 975,46" fill="#55e61f"/>
</svg>
<div class="toplinks"><span>About Us</span><span>History</span><span style="width:140px">Customer References</span><span>Blog</span><span>Contact</span></div>
<div class="topphone">
  <svg width="16" height="16" viewBox="0 0 24 24"><path d="M6.6 10.8a15 15 0 0 0 6.6 6.6l2.2-2.2a1 1 0 0 1 1-.25 11 11 0 0 0 3.6.6 1 1 0 0 1 1 1V20a1 1 0 0 1-1 1A17 17 0 0 1 3 4a1 1 0 0 1 1-1h3.5a1 1 0 0 1 1 1c0 1.25.2 2.45.6 3.6a1 1 0 0 1-.25 1z" fill="#55e61f"/></svg>
  <span style="color:#55e61f">+41 44 000 12 34</span>
</div>
<div class="header">
  <div class="logo" style="left:115px;top:10px;font-size:52px;line-height:64px">KAVRIN</div>
</div>
<div class="nav active" style="left:441px">Home</div>
<div class="nav" style="left:562px">eCommerce</div>
<div class="nav" style="left:738px">Online Marketing</div>
<div class="nav" style="left:973px">Integration</div>

<!-- hero -->
<section class="hero" role="img" aria-label="Photo of a smiling team working at computers in a modern office">
  <h1>Your online marketing<br>agency in Zurich for SMEs</h1>
  <p>You want to reach the right people online<br>and generate more sales. Contact us!</p>
  <div class="btn" style="left:113px;top:344px;width:279px;height:44px;font-size:16px">Appointment Calendar</div>
  <div class="arrow" style="left:42px">‹</div>
  <div class="arrow" style="left:1143px">›</div>
  <div class="dots" style="left:549px;top:497px"><i class="on"></i><i></i><i></i><i></i></div>
</section>
<svg class="abs" style="top:620px;left:0" width="1200" height="94" viewBox="0 0 1200 94">
  <polygon points="0,40 1200,20 1200,94 0,94" fill="#b9f77e"/>
  <polygon points="0,25 700,70 0,94" fill="#55e61f"/>
  <polygon points="0,94 1200,58 1200,94" fill="#fff"/>
</svg>

<!-- intro -->
<section class="intro">
  <h2 class="abs center" style="top:62px">The fast way to the online shop</h2>
  <p>Our goal is to give you added value with strategic online marketing – a technological competitive advantage that makes the difference. We build on automated processes for construction and operation your online shop. In this way, we shorten project times, bring web shops online faster and simplify operations. This is how you get to your new web branch quickly and easily. You sell – we take care of it online for the optimal conditions. As a holistically positioned online marketing agency, we offer you comprehensive advice and coaching for your new shop, for start-ups and restarts. Last but not least, we support Use our skills to find the right online marketing strategy for your business. Would you like to start your online shop quickly and successfully? We look forward to your call.</p>
  <div class="btn" style="left:524px;top:356px;width:150px;height:42px">Contact Us</div>
</section>

<!-- services -->
<section class="services">
  <h2 class="abs center" style="top:104px">Our services</h2>
  <div class="card" style="left:110px">
    <div class="icon" role="img" aria-label="Icon of a monitor with a shopping page"></div>
    <h3>Your successful entry<br>into Ecommerce</h3>
    <p>Do you want to sell your products or services online? But as an SME, don't you have a marketing department with e-commerce know-how?</p>
    <div class="btn">Learn More</div>
  </div>
  <div class="card featured" style="left:444px">
    <div class="icon" role="img" aria-label="Icon of a monitor with a shopping cart"></div>
    <h3>Our individual online<br>marketing solutions</h3>
    <p>In us you will find a dedicated team with passion, expertise and curiosity for all topics related to e-commerce and online marketing.</p>
    <div class="btn">Learn More</div>
  </div>
  <div class="card" style="left:779px">
    <div class="icon" role="img" aria-label="Icon of connected gears" style="background:#55e61f"></div>
    <h3>Integration</h3>
    <p style="top:180px">We take care of the special field of online marketing for you – you have a free hand for your core competencies and the good feeling about one reliable partner</p>
    <div class="btn">Learn More</div>
  </div>
</section>
<svg class="abs" style="top:1775px;left:0" width="1200" height="62" viewBox="0 0 1200 62">
  <polygon points="0,0 1200,40 1200,62 0,62" fill="#55e61f"/>
  <polygon points="250,60 1200,10 1200,62 0,62" fill="#b9f77e"/>
  <polygon points="0,62 1200,46 1200,62" fill="#e9efea"/>
</svg>

<!-- value -->
<section class="value">
  <h2 class="abs center" style="top:96px">Your added value</h2>
  <p class="center">We help companies to sell products and services in their own online shop within 3 weeks.<br>The result is more customers.</p>
  <div class="btn" style="left:525px;top:233px;width:147px;height:42px">Learn More</div>
  <svg class="abs" style="left:0;top:0" width="1200" height="655" viewBox="0 0 1200 655">
    <path d="M508 385 Q600 345 690 380" fill="none" stroke="#333" stroke-width="2" stroke-dasharray="2 4"/>
    <path d="M405 440 L335 490" fill="none" stroke="#333" stroke-width="2" stroke-dasharray="2 4"/>
    <path d="M790 440 L860 490" fill="none" stroke="#333" stroke-width="2" stroke-dasharray="2 4"/>
    <polygon points="660,430 820,437 820,450 665,446" fill="#55e61f"/>
    <polygon points="900,655 1200,605 1200,655" fill="#55e61f"/>
  </svg>
  <div class="node" style="left:392px;top:332px" role="img" aria-label="Systematic icon"><b></b></div>
  <div class="node on" style="left:688px;top:330px" role="img" aria-label="More customers icon"><b></b></div>
  <div class="node" style="left:229px;top:468px" role="img" aria-label="Automated icon"><b></b></div>
  <div class="node" style="left:851px;top:468px" role="img" aria-label="More sales icon"><b></b></div>
  <div class="nlabel" style="left:270px;top:378px">Systematic</div>
  <div class="nlabel" style="left:822px;top:376px;color:#55e61f">More customers</div>
  <div class="nlabel" style="left:108px;top:515px">Automated</div>
  <div class="nlabel" style="left:985px;top:515px">More sales</div>
</section>

<!-- contact -->
<section class="contact" role="img" aria-label="Photo of a support agent with headset in a call centre">
  <div class="form">
    <h3>CONTACT US</h3>
    <div class="field" style="left:29px;top:100px;width:205px;height:42px">First Name</div>
    <div class="field" style="left:242px;top:100px;width:206px;height:42px">Last Name</div>
    <div class="field" style="left:29px;top:152px;width:419px;height:42px">Email Address</div>
    <div class="field" style="left:29px;top:203px;width:419px;height:42px">Contact Number</div>
    <div class="field" style="left:29px;top:254px;width:419px;height:42px">Referance<span style="float:right">⌄</span></div>
    <div class="field" style="left:29px;top:306px;width:419px;height:104px">Message</div>
    <div class="btn">Submit</div>
  </div>
</section>

<!-- feedback -->
<svg class="abs" style="top:3168px;left:0" width="1200" height="60" viewBox="0 0 1200 60">
  <polygon points="0,0 1200,0 1200,3 0,55" fill="#b9f77e"/>
</svg>
<section class="feedback">
  <svg class="abs" style="top:0;left:0" width="1200" height="56"><polygon points="0,3 420,3 0,54" fill="#b9f77e"/></svg>
  <h2 class="abs center" style="top:85px">Customer Feedback</h2>
  <div class="fcard">
    <div class="thumb on" style="top:6px" role="img" aria-label="Portrait of the reviewer"><b></b></div>
    <div class="thumb" style="top:124px" role="img" aria-label="Portrait of another client"><b></b></div>
    <div class="thumb" style="top:242px" role="img" aria-label="Portrait of another client"><b></b></div>
    <svg class="quote" width="76" height="56" viewBox="0 0 76 56"><path d="M30 0v12c-9 2-13 7-13 16h13v28H0V30C0 12 10 2 30 0zM76 0v12c-9 2-13 7-13 16h13v28H46V30C46 12 56 2 76 0z" fill="#55e61f"/></svg>
    <div class="lead">Thank you for the really successful website lumen-praxis.de.</div>
    <div class="body">It fully meets my expectations. The cooperation was professional and uncomplicated. Again any time. Already have several positive feedbacks for the get page.</div>
    <div class="who">– Miriam Keller</div>
    <div class="role">owner of LUMEN occupational therapy<br>and speech therapy</div>
  </div>
</section>

<!-- team -->
<section class="team">
  <svg class="abs" style="top:0;left:0" width="1200" height="60"><polygon points="780,58 1200,0 1200,58" fill="#55e61f"/></svg>
  <h2 class="abs center" style="top:88px">Our Team</h2>
  <div class="member" style="left:190px">
    <div class="photo" role="img" aria-label="Portrait photo of Lukas Brandt"></div>
    <h3>Lukas Brandt</h3>
    <div class="role">(eCommerce Manager)</div>
    <div class="mail"><svg width="16" height="12" viewBox="0 0 16 12"><rect width="16" height="12" rx="1" fill="#55e61f"/><path d="M1 1l7 5 7-5" stroke="#272b28" fill="none"/></svg>lukas@kavrin.ch</div>
  </div>
  <div class="member" style="left:676px">
    <div class="photo" role="img" aria-label="Portrait photo of Jonas Feld"></div>
    <h3>Jonas Feld</h3>
    <div class="role">(Online Marketing Manager)</div>
    <div class="mail"><svg width="16" height="12" viewBox="0 0 16 12"><rect width="16" height="12" rx="1" fill="#55e61f"/><path d="M1 1l7 5 7-5" stroke="#272b28" fill="none"/></svg>jonas@kavrin.ch</div>
  </div>
</section>

<!-- partners -->
<section class="partners">
  <svg class="abs" style="top:0;left:0" width="1200" height="80"><polygon points="0,0 1200,0 0,75" fill="#55e61f"/><polygon points="0,0 1200,0 1200,0 0,40" fill="#b9f77e"/></svg>
  <div class="pbox" style="left:107px" role="img" aria-label="Partner badge"><b></b></div>
  <div class="pbox" style="left:359px" role="img" aria-label="Partner badge"><b></b></div>
  <div class="pbox" style="left:611px" role="img" aria-label="Partner badge"><b></b></div>
  <div class="pbox" style="left:864px" role="img" aria-label="Partner badge"><b></b></div>
  <div class="dots" style="left:555px;top:280px"><i class="on"></i><i></i><i></i></div>
  <svg class="abs" style="top:290px;left:0" width="1200" height="51"><polygon points="0,51 1200,0 1200,51" fill="#b9f77e"/><polygon points="600,51 1200,25 1200,51" fill="#55e61f"/></svg>
</section>

<!-- footer -->
<footer class="footer">
  <div class="logo" style="left:112px;top:88px;font-size:46px;line-height:58px">KAVRIN</div>
  <div class="finfo" style="top:187px"><svg width="14" height="18" viewBox="0 0 14 18"><path d="M7 0a7 7 0 0 1 7 7c0 5-7 11-7 11S0 12 0 7a7 7 0 0 1 7-7z" fill="#55e61f"/><circle cx="7" cy="7" r="2.5" fill="#1f2320"/></svg><span>Lindenweg 12, 8000 Zurich,<br>Switzerland</span></div>
  <div class="finfo" style="top:246px"><svg width="16" height="12" viewBox="0 0 16 12" style="margin-top:5px"><rect width="16" height="12" rx="1" fill="#55e61f"/><path d="M1 1l7 5 7-5" stroke="#1f2320" fill="none"/></svg><span>info@kavrin.ch</span></div>
  <div class="finfo" style="top:288px"><svg width="16" height="16" viewBox="0 0 24 24" style="margin-top:3px"><path d="M6.6 10.8a15 15 0 0 0 6.6 6.6l2.2-2.2a1 1 0 0 1 1-.25 11 11 0 0 0 3.6.6 1 1 0 0 1 1 1V20a1 1 0 0 1-1 1A17 17 0 0 1 3 4a1 1 0 0 1 1-1h3.5a1 1 0 0 1 1 1c0 1.25.2 2.45.6 3.6a1 1 0 0 1-.25 1z" fill="#55e61f"/></svg><span>+41 44 000 12 34</span></div>
  <div class="fcol" style="left:459px"><h4>Qucik Links</h4><a>Home</a><a>eCommerce</a><a>Online Marketing</a><a>Integration</a><a>Contact</a></div>
  <div class="fcol" style="left:700px"><h4>More Info</h4><a>About Us</a><a>History</a><a>Customer References</a><a>blog</a><a>Terms &amp; Conditions</a></div>
  <div class="fcol" style="left:963px"><h4>Explore</h4><a>Our Team</a><a>Newsletter</a><a>Services</a><a>Help &amp; Support</a><a>Privacy Policy</a></div>
  <div class="abs" style="left:0;top:345px;width:1200px;height:1px;background:#3a3f3b"></div>
  <div class="copy">Copyright © 2023 kavrin Marketing GmbH.</div>
</footer>

</body>
</html>
```